Velvet Moon Wheel Method Needs a Website

I require a Wordpress website so that I can do simple edits myself. I want it to be a fairly simple design as the videos and the text will speak for themselves.
The concept is simple, we have developed a revolutionary roulette system that proves the game is NOT random. This breakthrough is absolutely massive. We are offering a 12-part training course to take a beginner to a professional at their own pace through watching videos made by our roulette genius.
Roulette and casinos have a glitzy feel about them and this should be reflected in the style of the site. The roulette wheel, table and chips are very evocative and pictures of these would be good.
There is a home page and 5 other pages containing sub-pages. These should be interlinked and it must be easy to get back to the home page from anywhere on the site.
Coinvey links should appear at the bottom of each page.
I really need the site in a hurry as we were let down badly by the last developer we hired who went on holiday and left us in the lurch.

Target Market(s)

Gamblers, betting community, opportunity seekers

Coding

Coded - Design and coding required

Number of Pages Required

1 page

Font styles to use
Sans Serif

Requirements
Must have
• At least two videos on the Home page.
• Coinvey details on every page and tab.
• A box for name and email address for interested parties to leave their details.

```html
<!DOCTYPE html>
<html lang="en">
<head>
<meta charset="utf-8">
<title>Velvet Moon Wheel Method</title>
<link href="https://fonts.googleapis.com/css2?family=Oswald:wght@400;500&family=Open+Sans:wght@400;600;700&display=swap" rel="stylesheet">
<style>
:root{
  --red:#e3121b;
  --red-dark:#b80d14;
  --ink:#1d2530;
  --ink-deep:#151b23;
  --text:#555c63;
  --muted:#8b9096;
  --light:#f3f4f5;
  --white:#fff;
  --grey:#707070;
}
*{box-sizing:border-box;margin:0;padding:0}
html,body{width:1200px;height:3087px;overflow:hidden}
body{font-family:"Open Sans",Arial,sans-serif;color:var(--text);background:var(--white);position:relative}
.wrap{width:1030px;margin:0 auto;position:relative;height:100%}
section,header,footer,nav{position:relative;width:1200px}
h2.title{font-family:"Oswald",Arial,sans-serif;font-weight:400;font-size:29px;color:var(--ink)}
h2.title em{font-style:normal;color:var(--red)}
p{font-size:12.5px;line-height:25px}

/* header */
.topbar{height:103px;background:var(--ink)}
.brand{position:absolute;left:50%;top:32px;transform:translateX(-50%);display:flex;align-items:center;gap:12px}
.brand-dot{width:34px;height:34px;border-radius:50%;background:var(--red)}
.brand-name{font-family:"Oswald",Arial,sans-serif;font-size:24px;color:var(--white);white-space:nowrap}
.mainnav{height:62px;background:var(--red)}
.mainnav ul{list-style:none;position:absolute;left:108px;top:0;height:62px;display:flex;align-items:center}
.mainnav li{font-weight:700;font-size:13.5px;color:var(--white);padding:0 22px;border-right:1px solid rgba(255,255,255,.45);line-height:16px;white-space:nowrap}
.mainnav li:last-child{border-right:0}
.cart{position:absolute;left:944px;top:0;height:62px;width:170px;background:var(--red-dark);display:flex;align-items:center;gap:10px;padding-left:12px;color:var(--white);font-size:10.5px;font-weight:700;line-height:15px}

/* hero */
.hero{height:483px;background:radial-gradient(circle at 30% 40%,#7a5a35 0%,#3d2a1c 35%,#1c1410 70%,#0e0b09 100%)}
.hero-art{position:absolute;inset:0}
.hero-copy{position:absolute;left:760px;top:150px;width:380px;color:var(--white)}
.hero-copy h1{font-family:"Oswald",Arial,sans-serif;font-weight:400;font-size:33px;line-height:44px;margin-bottom:12px;white-space:nowrap}
.hero-copy h1 em{font-style:normal;color:var(--red)}
.hero-copy p{font-size:11.5px;line-height:24px;color:#e8e8e8;width:330px}
.btn-red{display:inline-block;background:var(--red);color:var(--white);font-family:"Oswald",Arial,sans-serif;font-size:16px;padding:9px 30px;margin-top:20px}
.dots{position:absolute;left:1024px;top:443px;display:flex;gap:8px}
.dots span{width:14px;height:14px;border-radius:50%;border:2px solid var(--white)}
.dots span.on{background:var(--red);border-color:var(--red)}

/* welcome */
.welcome{height:402px}
.welcome-copy{position:absolute;left:0;top:42px;width:540px}
.welcome-copy h2{margin-bottom:28px}
.welcome-copy p{margin-bottom:20px;font-size:11.5px;line-height:24px}
.link-red{font-weight:700;font-size:15px;color:var(--red);border-bottom:2px solid var(--red);padding-bottom:2px;display:inline-flex;align-items:center;gap:8px}
.video{position:absolute;left:587px;top:48px;width:440px;height:308px;background:linear-gradient(160deg,#6a4c3a 0%,#2f6b44 45%,#17492c 100%)}
.play{position:absolute;left:50%;top:45%;transform:translate(-50%,-50%);width:44px;height:32px;background:var(--red);border-radius:8px}
.play:after{content:"";position:absolute;left:17px;top:9px;border-left:13px solid #fff;border-top:7px solid transparent;border-bottom:7px solid transparent}
.video-bar{position:absolute;left:0;right:0;bottom:0;height:34px;background:#161616;color:#ccc;font-size:10px;display:flex;align-items:center;padding-left:46px}
.video-bar:before{content:"";position:absolute;left:0;right:0;top:0;height:4px;background:var(--red)}

/* training */
.training{height:457px;background:var(--light)}
.centered{text-align:center}
.training h2{padding-top:36px}
.intro{width:680px;margin:14px auto 0;font-size:11.5px;line-height:26px;text-align:center}
.features{display:grid;grid-template-columns:repeat(4,1fr);position:absolute;left:0;right:0;top:164px}
.feature{text-align:center;padding:0 18px}
.feature svg{display:block;margin:0 auto 20px}
.feature h3{font-family:"Oswald",Arial,sans-serif;font-weight:400;font-size:17px;color:var(--ink);margin-bottom:12px}
.feature h3.hot{color:var(--red)}
.feature p{font-size:11px;line-height:25px}

/* casinos */
.casinos{height:397px;background:var(--red)}
.tabs{position:absolute;left:0;top:119px;width:264px;list-style:none}
.tabs li{height:55px;line-height:55px;background:#1f1f1f;color:var(--white);font-weight:700;font-size:15px;padding-left:20px}
.tabs li.active{background:var(--red-dark);box-shadow:0 4px 10px rgba(0,0,0,.35)}
.casino-copy{position:absolute;left:324px;top:40px;width:680px;color:var(--white)}
.casino-copy h2{color:var(--white);font-size:26px;margin-bottom:14px}
.casino-copy p{font-size:11.5px;line-height:24px}
.partners{position:absolute;left:330px;top:192px;display:flex;gap:120px}
.partner{width:94px;text-align:center;color:var(--white);font-weight:700;font-size:15px}
.partner .ring{width:94px;height:94px;border:2px solid var(--white);border-radius:50%;display:flex;align-items:center;justify-content:center;margin-bottom:16px}

/* plan */
.plan{height:405px;background:#fafafa}
.plan-copy{position:absolute;left:23px;top:68px;width:300px}
.plan-copy h2{margin-bottom:12px}
.plan-copy p{font-size:11.5px;line-height:24px;margin-bottom:14px}
.card{position:absolute;top:37px;width:300px;height:331px;background:var(--white);border:1px solid #e3e3e3;box-shadow:0 1px 4px rgba(0,0,0,.08);text-align:center}
.card .badge{width:34px;height:34px;border-radius:50%;background:var(--grey);margin:14px auto 12px;display:flex;align-items:center;justify-content:center}
.card h4{font-weight:400;font-size:14px;color:#555;letter-spacing:.5px;margin-bottom:12px}
.price{background:var(--grey);color:var(--white);font-weight:700;font-size:25px;height:45px;line-height:45px}
.price small{font-size:14px;font-weight:400}
.card ul{list-style:none;margin-top:4px}
.card li{font-size:11.5px;color:var(--muted);height:36px;line-height:36px;border-bottom:1px solid #eee;margin:0 14px}
.btn-grey{display:inline-block;background:var(--grey);color:var(--white);font-size:11px;font-weight:700;padding:6px 20px;margin-top:16px;border:1px solid #555}

/* vegas */
.vegas{height:350px;background:linear-gradient(180deg,#2a2a2c 0%,#3a3a3c 50%,#232325 100%)}
.vegas-art{position:absolute;inset:0}
.vegas-copy{position:absolute;left:0;right:0;top:66px;text-align:center;color:var(--white)}
.vegas-copy h2{font-family:"Oswald",Arial,sans-serif;font-weight:400;font-size:26px;margin-bottom:10px}
.vegas-copy h2 em{font-style:normal;color:var(--red)}
.vegas-copy p{width:680px;margin:0 auto;font-size:11.5px;line-height:24px}
.btn-outline{display:inline-block;border:2px solid #ccc;color:var(--white);font-weight:700;font-size:12.5px;padding:13px 20px;margin-top:28px;border-radius:3px}

/* newsletter */
.newsletter{height:99px;background:var(--red)}
.newsletter .inner{position:absolute;left:252px;top:28px;display:flex;align-items:center;gap:16px}
.newsletter h3{font-family:"Oswald",Arial,sans-serif;font-weight:400;font-size:26px;color:var(--white)}
.field{width:360px;height:40px;background:var(--white);border-radius:20px;font-size:12px;color:#777;line-height:40px;padding-left:22px}
.btn-dark{width:150px;height:40px;border-radius:20px;background:#222;color:var(--white);font-size:12px;text-align:center;line-height:40px;box-shadow:inset 0 -3px 0 #000}

/* footer */
.footer{height:257px;background:var(--light)}
.foot-brand{position:absolute;left:0;top:100px;display:flex;align-items:center;gap:12px}
.foot-brand .brand-name{color:var(--ink);font-size:22px}
.col{position:absolute;top:36px}
.col h5{font-weight:600;font-size:15px;color:#444;letter-spacing:.5px;margin-bottom:22px}
.col li{list-style:none;font-size:11.5px;color:#555;line-height:25px;display:flex;align-items:center;gap:12px}
.links li{gap:14px}
.socials{display:flex;gap:10px;margin-top:24px}
.socials span{width:32px;height:32px;border-radius:50%;border:1.5px solid #999}
.copyright{height:72px;background:var(--ink-deep);color:#cfcfcf;font-size:11px;text-align:center;line-height:72px}
</style>
</head>
<body>

<header class="topbar">
  <div class="brand"><span class="brand-dot"></span><span class="brand-name">Velvet Moon Wheel Method</span></div>
</header>

<nav class="mainnav">
  <ul>
    <li>HOME</li><li>VELVET MOON TRAINING</li><li>CASINOS</li><li>COACHING</li><li>LAS VEGAS</li><li>CONTACT US</li>
  </ul>
  <div class="cart">
    <svg width="30" height="26" viewBox="0 0 30 26" fill="none" stroke="#fff" stroke-width="2"><path d="M1 3h5l4 14h15l3-10H8"/><circle cx="12" cy="22" r="2"/><circle cx="23" cy="22" r="2"/></svg>
    <span>SHOPPING CART IS<br>(0) ITEMS</span>
  </div>
</nav>

<section class="hero">
  <div class="hero-art" role="img" aria-label="Close-up photo of a spinning roulette wheel with ball, golden lighting"></div>
  <div class="hero-copy">
    <h1>Velvet Moon <em>Wheel Method</em></h1>
    <p>Introducing the incredible Velvet Moon roulette system. Four years in the making by a roulette genius who has observed hundreds of thousands of spins to create a truly ground breaking sys tem very aspect</p>
    <span class="btn-red">Read More</span>
  </div>
  <div class="dots"><span></span><span></span><span class="on"></span><span></span></div>
</section>

<section class="welcome">
  <div class="wrap">
    <div class="welcome-copy">
      <h2 class="title">Welcome To <em>Velvet Moon</em></h2>
      <p>Introducing the incredible Velvet Moon roulette system. Four years in the making by a roulette genius who has observed hundreds of thousands of spins to create a truly groundbreaking system. Every aspect of the game has been broken down, analysed and rebuilt with a solution. This system questions whether the game of roulette is truly random.</p>
      <p>The key to success is long term profits but to achieve that you need to look beyond complexity &amp; concentrate on simplicity. The system reverses general logic and considers the number of losses fully balanced approach to progression that protects your bankroll at all times.</p>
      <span class="link-red">WATCH VIDEO
        <svg width="14" height="14" viewBox="0 0 14 14"><circle cx="7" cy="7" r="7" fill="#e3121b"/><path d="M5.5 4l3 3-3 3" stroke="#fff" stroke-width="1.8" fill="none"/></svg>
      </span>
    </div>
    <div class="video" role="img" aria-label="Video still of players gathered around a green casino gaming table">
      <span class="play"></span>
      <div class="video-bar">0:00 / 3:00</div>
    </div>
  </div>
</section>

<section class="training">
  <div class="wrap centered">
    <h2 class="title">Our <em>Training</em></h2>
    <p class="intro">Introducing the incredible Velvet Moon roulette system. Four years in the making by a roulette genius who has observed hundreds of thousands of spins to create a truly groundbreaking system.</p>
    <div class="features">
      <div class="feature">
        <svg width="100" height="100" viewBox="0 0 100 100"><circle cx="50" cy="50" r="48" fill="#333"/><circle cx="50" cy="50" r="38" fill="#fff"/><circle cx="50" cy="50" r="44" fill="none" stroke="#fff" stroke-width="4" stroke-dasharray="10 12"/><circle cx="50" cy="50" r="16" fill="none" stroke="#333" stroke-width="3"/><path d="M50 40v10l7 5" stroke="#333" stroke-width="3" fill="none"/></svg>
        <h3>Course Description</h3>
        <p>Introducing the incredible Velvet Moon roulette system. Four years in the maki truly groundbreaking system.</p>
      </div>
      <div class="feature">
        <svg width="100" height="100" viewBox="0 0 100 100"><circle cx="50" cy="50" r="48" fill="#e3121b"/><circle cx="50" cy="50" r="38" fill="#fff"/><circle cx="50" cy="50" r="44" fill="none" stroke="#fff" stroke-width="4" stroke-dasharray="10 12"/><rect x="36" y="36" width="28" height="28" rx="3" fill="none" stroke="#e3121b" stroke-width="3"/><path d="M36 45h28" stroke="#e3121b" stroke-width="3"/></svg>
        <h3 class="hot">Monthly Membership</h3>
        <p>Introducing the incredible Velvet Moon roulette system. Four years in the maki truly groundbreaking system.</p>
      </div>
      <div class="feature">
        <svg width="100" height="100" viewBox="0 0 100 100"><circle cx="50" cy="50" r="48" fill="#333"/><circle cx="50" cy="50" r="38" fill="#fff"/><circle cx="50" cy="50" r="44" fill="none" stroke="#fff" stroke-width="4" stroke-dasharray="10 12"/><rect x="34" y="38" width="32" height="20" rx="2" fill="none" stroke="#333" stroke-width="3"/><path d="M30 63h40" stroke="#333" stroke-width="3"/><path d="M42 48l5 5 9-9" stroke="#333" stroke-width="3" fill="none"/></svg>
        <h3>The Complete System</h3>
        <p>Introducing the incredible Velvet Moon roulette system. Four years in the maki truly groundbreaking system.</p>
      </div>
      <div class="feature">
        <svg width="100" height="100" viewBox="0 0 100 100"><circle cx="50" cy="50" r="48" fill="#e3121b"/><circle cx="50" cy="50" r="38" fill="#fff"/><circle cx="50" cy="50" r="44" fill="none" stroke="#fff" stroke-width="4" stroke-dasharray="10 12"/><circle cx="50" cy="45" r="11" fill="none" stroke="#e3121b" stroke-width="3"/><path d="M45 59h10M46 64h8" stroke="#e3121b" stroke-width="3"/></svg>
        <h3 class="hot">Intellectual Property</h3>
        <p>Introducing the incredible Velvet Moon roulette system. Four years in the maki truly groundbreaking system.</p>
      </div>
    </div>
  </div>
</section>

<section class="casinos">
  <div class="wrap">
    <ul class="tabs">
      <li class="active">REPUTABLE CASINOS</li>
      <li>CASINO BONUSES</li>
      <li>RNG VS REAL WHEEL</li>
    </ul>
    <div class="casino-copy">
      <h2 class="title">Our Casinos</h2>
      <p>The second major breakthrough was the discovery of the families. These are groups of numbers that appear regularly within a few spins of each other. For students learning the system, this is their first 'wow' moment. The regularity of hits between numbers in the families is staggering and underpins the whole system.</p>
    </div>
    <div class="partners">
      <div class="partner"><div class="ring"><svg width="40" height="40" viewBox="0 0 40 40" fill="#fff"><circle cx="26" cy="11" r="6"/><path d="M4 30l8-6h10l6-4 3 3-9 8H8z"/></svg></div>LUCKYHALL</div>
      <div class="partner"><div class="ring"><svg width="40" height="40" viewBox="0 0 40 40"><rect x="6" y="12" width="20" height="20" rx="3" fill="#fff"/><rect x="18" y="6" width="16" height="16" rx="3" fill="#fff" stroke="#e3121b" stroke-width="2"/><circle cx="12" cy="18" r="2" fill="#e3121b"/><circle cx="20" cy="26" r="2" fill="#e3121b"/><circle cx="26" cy="14" r="2" fill="#e3121b"/></svg></div>REDCROWN</div>
      <div class="partner"><div class="ring"><svg width="44" height="16" viewBox="0 0 44 16" fill="none" stroke="#fff" stroke-width="2.5"><circle cx="7" cy="8" r="5"/><circle cx="22" cy="8" r="5"/><circle cx="37" cy="8" r="5"/></svg></div>ETC</div>
    </div>
  </div>
</section>

<section class="plan">
  <div class="wrap">
    <div class="plan-copy">
      <h2 class="title">Our <em>plan</em></h2>
      <p>The system reverses general logic and considers the number of losses rather than the number of wins. This led to the discovery of the counting system, a perfect, carefully balanced approach to progression that prot ects your bankroll at all times.</p>
      <p>This led to the discovery of the counting system, a per fect, carefully balanced approach to progression that prot ects your bankroll at all times.</p>
    </div>
    <div class="card" style="left:371px">
      <div class="badge"><svg width="14" height="14" viewBox="0 0 24 24" fill="#fff"><path d="M12 2l3 7 7 .6-5.3 4.6 1.7 7.3L12 17.8 5.6 21.5l1.7-7.3L2 9.6 9 9z"/></svg></div>
      <h4>MONTHLY SUBSCRIPTION</h4>
      <div class="price">£100.00 <small>/ month</small></div>
      <ul><li>Monthly membership is to</li><li>Release a new video every</li><li>Month which builds on what</li></ul>
      <span class="btn-grey">SIGNUP</span>
    </div>
    <div class="card" style="left:704px">
      <div class="badge"><svg width="14" height="14" viewBox="0 0 24 24" fill="#fff"><path d="M12 2l3 7 7 .6-5.3 4.6 1.7 7.3L12 17.8 5.6 21.5l1.7-7.3L2 9.6 9 9z"/></svg></div>
      <h4>SINGLE PAYMENT</h4>
      <div class="price">£1000.00 <small>/ month</small></div>
      <ul><li>Monthly membership is to</li><li>Release a new video every</li><li>Month which builds on what</li></ul>
      <span class="btn-grey">SIGNUP</span>
    </div>
  </div>
</section>

<section class="vegas">
  <div class="vegas-art" role="img" aria-label="Dark monochrome photo of the Las Vegas skyline at night"></div>
  <div class="vegas-copy">
    <h2>LAS <em>VEGAS</em></h2>
    <p>The system reverses general logic and considers the number of losses rather than the number of wins. This led to the discovery of the counting system, a perfect, carefully balanced approach to progression that protects your bankroll at all when combined with the rules of Velvet Moon, it's dynamite.</p>
    <span class="btn-outline">CLICK HERE FOR MORE INFO</span>
  </div>
</section>

<section class="newsletter">
  <div class="inner">
    <h3>SUBSCRIBE NEWSLETTER :</h3>
    <div class="field">Enter Your Email Id :</div>
    <div class="btn-dark">SUBSCRIBE</div>
  </div>
</section>

<footer class="footer">
  <div class="wrap">
    <div class="foot-brand"><span class="brand-dot"></span><span class="brand-name">Velvet Moon Wheel Method</span></div>
    <div class="col" style="left:330px">
      <h5>CONTACT US</h5>
      <ul>
        <li><svg width="14" height="12" viewBox="0 0 14 12" fill="#666"><rect x="1" y="3" width="12" height="9" rx="1"/><rect x="3" y="0" width="8" height="4"/></svg>07900 123456 (Phone)</li>
        <li><svg width="14" height="12" viewBox="0 0 14 12" fill="#666"><rect x="1" y="2" width="12" height="10" rx="1"/></svg>011 555 01 99 (Fax)</li>
        <li><svg width="14" height="12" viewBox="0 0 14 12" fill="none" stroke="#666" stroke-width="1.5"><rect x="1" y="2" width="12" height="9"/><path d="M1 2l6 5 6-5"/></svg><span style="color:#2a5db0;text-decoration:underline">support@velvetmoonmethod.com</span></li>
        <li style="align-items:flex-start;line-height:20px;margin-top:3px"><svg width="14" height="14" viewBox="0 0 14 14" fill="#666" style="margin-top:3px"><path d="M7 0a5 5 0 015 5c0 4-5 9-5 9S2 9 2 5a5 5 0 015-5z"/></svg><span>#45 Harbour Lane, 2nd Cross<br>Velvet Moon</span></li>
      </ul>
    </div>
    <div class="col links" style="left:600px">
      <h5>QUICK LINKS</h5>
      <ul>
        <li><span>»</span>HOME</li><li><span>»</span>VELVET MOON TRAINING</li><li><span>»</span>CASINOS</li><li><span>»</span>COACHING</li><li><span>»</span>LAS VEGAS</li><li><span>»</span>Contact Us</li>
      </ul>
    </div>
    <div class="col" style="left:822px;width:200px">
      <h5>FOLLOW US</h5>
      <p style="font-size:11.5px;line-height:20px;color:#555">Every aspect of the game has been broken down, analysed and rebuilt with a solution.</p>
      <div class="socials"><span></span><span></span><span></span><span></span><span></span></div>
    </div>
  </div>
</footer>

<div class="copyright">© Copyright 2016 Velvet Moon Wheel Method. All Rights Reserved</div>

</body>
</html>
```